life insurance quote website design for lepontdoriole.ca

the web site lepontdoriole.ca need a design. we dont like the actuel one but we are open at all new suggestion. visit us at lepontdoriole.ca and you will understand. the principal concurant is tarifsgarantisnord.ca, calculeo.ca, coutprotecfam.ca. We are a life insurance quote site. we found best price available in the canadien industrie. We absolutly want a design with our form in the front page on the top right side like our concurance, we use wordpress at this time. we want to be able to switch language. and to have a logic form. we want to be able to change the color for each type of insurance quote page.we also need a blog in it to post news. and the site will be SEO accurate.

Target Market(s)

Get client fill the quote form

Industry/Entity Type

Insurance

Number of Pages Required

3 page

Font styles to use
Sans Serif

Requirements
Must have
• logic form on the top right first page
• page template for product info stuff, contact, and who we are, blog
• French site
• custum color
Nice to have
• Wordpress design will be appréciate
• switch language english/french

```html
<!DOCTYPE html>
<html lang="fr">
<head>
<meta charset="utf-8">
<title>lepontdoriole.ca — Soumission assurance vie</title>
<link href="https://fonts.googleapis.com/css2?family=Raleway:wght@400;500;600;700&display=swap" rel="stylesheet">
<style>
:root{
  --blue:#0b63b8;
  --blue-dark:#084f95;
  --red:#d9201f;
  --ink:#333;
  --muted:#555;
  --dark:#2b2b2b;
  --footer:#333;
  --gray-band:#ebebeb;
  --line:#cfcfcf;
  --c-vie:#2fb2de;
  --c-salaire:#dca444;
  --c-hypo:#5cbd55;
  --c-graves:#ec5b85;
  --white:#fff;
}
*{box-sizing:border-box;margin:0;padding:0}
html,body{width:1200px;height:2913px;overflow:hidden}
body{font-family:'Raleway',sans-serif;color:var(--ink);background:var(--white);position:relative}
.abs{position:absolute}

/* header */
.topbar{position:absolute;left:0;top:0;width:1200px;height:92px;background:var(--white)}
.lang{left:101px;top:32px;width:88px;height:32px;border:1px solid var(--line);font-size:15px;display:flex;align-items:center;gap:6px;padding-left:8px}
.lang .sq{width:24px;height:16px;background:#9aa6c4}
.social{top:28px;width:40px;height:40px;border:1.5px solid #444;border-radius:50%}
.login-field{top:33px;height:34px;border:1px solid #bbb;border-radius:3px;font-size:14px;color:#777;padding:8px 10px}
.login-btn{left:1012px;top:33px;width:87px;height:34px;background:var(--blue);color:#fff;font-size:15px;border-radius:3px;display:flex;align-items:center;justify-content:center}
.nav{position:absolute;left:0;top:92px;width:1200px;height:67px;background:linear-gradient(var(--blue),var(--blue-dark))}
.nav a{position:absolute;top:24px;color:#fff;font-size:16px;font-weight:500;text-decoration:none}
.nav .sep{position:absolute;top:14px;width:1px;height:40px;background:rgba(255,255,255,.25)}
.brand-disc{left:520px;top:0;width:160px;height:160px;border-radius:50%;background:#fff;display:flex;align-items:center;justify-content:center;flex-direction:column;gap:6px}
.brand-dot{width:22px;height:22px;border-radius:50%;background:var(--red)}
.brand-name{font-size:17px;font-weight:700;color:var(--red)}

/* hero */
.hero-photo{left:0;top:159px;width:1200px;height:492px;background:linear-gradient(180deg,#8fb95a 0%,#b6d48a 45%,#dfe6d8 62%,#7fae3c 100%)}
.hero-arrow{top:388px;width:36px;height:36px;border-radius:50%;border:1.5px solid #333;background:rgba(255,255,255,.5);display:flex;align-items:center;justify-content:center}

/* quote form */
.quote{left:720px;top:218px;width:433px;height:772px}
.quote svg.frame{position:absolute;left:0;top:0}
.quote-head{position:absolute;left:3px;top:3px;width:427px;height:56px;background:var(--red);color:#fff;font-size:21px;font-weight:600;display:flex;align-items:center;justify-content:center}
.q-sec{position:absolute;left:18px;font-size:17px;font-weight:700;color:#222;width:395px;border-bottom:2px solid #999;padding-bottom:8px}
.q-lab{position:absolute;font-size:15px;color:#444;text-align:right;width:150px;left:0}
.q-lab b{color:var(--red);font-weight:400;font-size:11px;vertical-align:top}
.q-in{position:absolute;left:168px;width:192px;height:36px;border:1px solid #aaa;border-radius:3px;font-size:13px;color:#777;padding:9px 10px}
.q-radio{position:absolute;font-size:13px;color:#444;display:flex;align-items:center;gap:8px}
.q-radio i{width:12px;height:12px;border:1px solid #999;border-radius:50%;display:inline-block}
.captcha-word{position:absolute;left:78px;top:645px;font-size:22px;font-weight:700;font-style:italic;color:#222}
.send{position:absolute;left:166px;top:688px;width:114px;height:38px;background:var(--red);color:#fff;font-size:14px;display:flex;align-items:center;justify-content:center;border-radius:3px}

/* intro */
.intro-mark{left:99px;top:680px;width:70px;height:70px;display:flex;align-items:center;justify-content:center}
.intro-title{left:190px;top:682px;width:440px;font-size:26px;font-weight:500;line-height:1.35;color:#222}
.intro-text{left:99px;top:776px;width:568px;font-size:13px;line-height:1.75;color:var(--muted);text-align:justify}
.ticks{left:99px;top:896px;list-style:none}
.ticks li{font-size:14px;color:#444;height:29px;display:flex;align-items:center;gap:14px}

/* key features */
.features{left:0;top:1068px;width:1200px;height:408px;background:linear-gradient(180deg,#232323,#1c1c1c)}
.sec-head{display:flex;gap:22px;align-items:center}
.sec-head .dot{width:52px;height:52px;border-radius:50%;background:var(--red)}
.sec-head h2{font-size:26px;font-weight:500}
.sec-head p{font-size:14px;margin-top:4px}
.feat-card{top:1291px;width:235px;height:101px;color:#fff;font-size:21px;font-weight:700;display:flex;align-items:flex-end;justify-content:center;padding-bottom:22px;border-bottom:8px solid rgba(0,0,0,.15)}
.feat-icon{top:1227px;width:98px;height:98px;border-radius:50%;border:5px solid #fff;display:flex;align-items:center;justify-content:center}
.feat-cta{top:1412px;width:235px;text-align:center;color:#fff;font-size:21px;font-weight:500}

/* blog */
.post{top:1618px;width:307px;height:359px;background:#fff;box-shadow:0 0 6px rgba(0,0,0,.18);border-bottom:4px solid var(--blue)}
.post .ph{height:180px}
.post .date{position:absolute;left:18px;top:192px;font-size:11px;color:#444;display:flex;gap:8px;align-items:center}
.post h3{position:absolute;left:18px;top:220px;width:270px;font-size:16px;font-weight:600;color:#222;border-bottom:1px solid #ddd;padding-bottom:8px}
.post p{position:absolute;left:18px;top:258px;width:270px;font-size:13px;line-height:1.6;color:var(--muted);text-align:justify}
.post .more{position:absolute;right:18px;top:322px;font-size:13px;color:#333}

/* assurance vie */
.vie-band{left:0;top:2020px;width:1200px;height:340px;background:var(--gray-band)}
.vie-brand{left:87px;top:2100px;width:280px;display:flex;align-items:center;gap:12px}
.vie-brand .brand-name{font-size:24px}
.vie-title{left:388px;top:2066px;font-size:23px;color:var(--red);font-weight:500}
.vie-sub{left:388px;top:2108px;font-size:15px;color:#333}
.vie-text{left:388px;top:2146px;width:722px;font-size:12.5px;line-height:1.7;color:var(--muted)}
.vie-ticks{font-size:14px;color:#444;display:flex;gap:14px;align-items:flex-start;line-height:1.5}

/* contact strip */
.contact-line{left:165px;font-size:15px;line-height:1.75;color:#444}
.contact-line strong{color:var(--red);font-weight:600}
.partner-badge{left:835px;top:2410px;width:223px;height:130px;display:flex;flex-direction:column;align-items:center;gap:14px}

/* footer */
.footer{left:0;top:2573px;width:1200px;height:278px;background:var(--footer);color:#fff}
.f-h{font-size:15px;font-weight:600;color:#fff}
.f-item{font-size:13px;color:#fff;line-height:1.5}
.f-list{list-style:none}
.f-list li{font-size:13px;height:29px}
.f-in{width:224px;height:34px;border:1px solid #888;font-size:12px;color:#ccc;padding:9px 10px}
.f-btn{width:224px;height:36px;background:var(--blue);color:#fff;font-size:13px;display:flex;align-items:center;justify-content:center}
.bottom{left:0;top:2851px;width:1200px;height:62px;background:linear-gradient(var(--blue),var(--blue-dark));color:#fff;font-size:14px;display:flex;align-items:center;justify-content:center}
</style>
</head>
<body>

<!-- header -->
<header class="topbar">
  <div class="abs lang"><span class="sq"></span>ENG ▾</div>
  <span class="abs social" style="left:213px"></span>
  <span class="abs social" style="left:265px"></span>
  <span class="abs social" style="left:318px"></span>
  <div class="abs login-field" style="left:709px;width:140px">Email</div>
  <div class="abs login-field" style="left:857px;width:139px">Password</div>
  <div class="login-btn abs">Login</div>
</header>
<nav class="nav">
  <a style="left:128px">HOME</a>
  <span class="sep" style="left:203px"></span>
  <a style="left:228px">PRODUCTS</a>
  <span class="sep" style="left:344px"></span>
  <a style="left:370px">SUBMISSION</a>
  <span class="sep" style="left:483px"></span>
  <a style="left:750px">WHO WE ARE</a>
  <span class="sep" style="left:900px"></span>
  <a style="left:948px">CONTACT US</a>
</nav>
<div class="abs brand-disc"><span class="brand-dot"></span><span class="brand-name">lepontdoriole.ca</span></div>

<!-- hero -->
<div class="abs hero-photo" role="img" aria-label="Photo d'une famille souriante allongée dans l'herbe au soleil"></div>
<div class="abs hero-arrow" style="left:12px"><svg width="12" height="12" viewBox="0 0 12 12"><path d="M8 1 3 6l5 5" fill="none" stroke="#333" stroke-width="1.6"/></svg></div>
<div class="abs hero-arrow" style="left:1147px"><svg width="12" height="12" viewBox="0 0 12 12"><path d="M4 1l5 5-5 5" fill="none" stroke="#333" stroke-width="1.6"/></svg></div>

<form class="abs quote">
  <svg class="frame" width="433" height="772" viewBox="0 0 433 772"><polygon points="1.5,1.5 431.5,1.5 431.5,700 216.5,770 1.5,700" fill="#fff" stroke="#555" stroke-width="3"/></svg>
  <div class="quote-head">QUOTE REQUEST</div>
  <div class="q-sec" style="top:82px">Product:</div>
  <div class="q-lab" style="top:136px;left:-2px;width:152px;text-align:left;padding-left:16px">Types of insurance:<b>*</b></div>
  <div class="q-in" style="top:127px">Select <span style="float:right;color:#333">▼</span></div>
  <div class="q-sec" style="top:182px">Applicant:</div>
  <div class="q-lab" style="top:238px">Full Name:<b>*</b></div><div class="q-in" style="top:229px"></div>
  <div class="q-lab" style="top:281px">Cities:<b>*</b></div><div class="q-in" style="top:272px"></div>
  <div class="q-lab" style="top:324px">Email:<b>*</b></div><div class="q-in" style="top:315px"></div>
  <div class="q-lab" style="top:367px">Phone:<b>*</b></div>
  <div class="q-lab" style="top:410px">Age:<b>*</b></div><div class="q-in" style="top:401px"></div>
  <div class="q-lab" style="top:460px">Gender:<b>*</b></div>
  <div class="q-radio" style="left:168px;top:462px"><i></i>Man</div>
  <div class="q-radio" style="left:252px;top:462px"><i></i>Wife</div>
  <div class="q-sec" style="top:500px">Co-Applicant:</div>
  <div class="q-radio" style="left:18px;top:552px"><i></i>Add a co-applicant</div>
  <div class="q-radio" style="left:18px;top:584px;width:280px;align-items:flex-start;line-height:1.7"><i style="margin-top:5px;flex:none"></i>I Have Read And Accept The Use And Privacy Policy</div>
  <div class="q-lab" style="top:652px;width:68px">Captcha:</div>
  <div class="captcha-word">viearet</div>
  <div class="q-in" style="top:642px"></div>
  <div class="send">Send Now</div>
</form>

<!-- intro -->
<div class="abs intro-mark"><span class="brand-dot" style="width:40px;height:40px"></span></div>
<h1 class="abs intro-title">Trouvez la meilleure assurance, au meilleur prix!</h1>
<p class="abs intro-text">Que vous soyez à la recherche d'une assurance vie, d'une assurance hypothécaire ou autre, vous désirez très certainement payer le prix le plus avantageux. S'y retrouver parmi les offres nombreuses du domaine de l'assurance peut être un véritable casse-tête. Mais grâce à l'intervention des conseillers en sécurité financière de lepontdoriole.ca, vous vous épargnerez des heures de recherche infructueuse, et, de plus,</p>
<ul class="abs ticks">
  <li><svg width="16" height="16" viewBox="0 0 16 16"><circle cx="8" cy="8" r="7" fill="none" stroke="#d9201f" stroke-width="1.5"/><path d="M4.5 8.2 7 10.5l4.5-5" fill="none" stroke="#d9201f" stroke-width="1.6"/></svg>Assurance vie permanente – Assurance vie temporaire</li>
  <li><svg width="16" height="16" viewBox="0 0 16 16"><circle cx="8" cy="8" r="7" fill="none" stroke="#d9201f" stroke-width="1.5"/><path d="M4.5 8.2 7 10.5l4.5-5" fill="none" stroke="#d9201f" stroke-width="1.6"/></svg>Assurance invalidité – Assurance salaire</li>
  <li><svg width="16" height="16" viewBox="0 0 16 16"><circle cx="8" cy="8" r="7" fill="none" stroke="#d9201f" stroke-width="1.5"/><path d="M4.5 8.2 7 10.5l4.5-5" fill="none" stroke="#d9201f" stroke-width="1.6"/></svg>Assurance prêt hypothécaire – Assurance prêts</li>
  <li><svg width="16" height="16" viewBox="0 0 16 16"><circle cx="8" cy="8" r="7" fill="none" stroke="#d9201f" stroke-width="1.5"/><path d="M4.5 8.2 7 10.5l4.5-5" fill="none" stroke="#d9201f" stroke-width="1.6"/></svg>Assurance maladies graves</li>
</ul>

<!-- key features -->
<section class="abs features"></section>
<div class="abs sec-head" style="left:486px;top:1096px;color:#fff"><span class="dot"></span><div><h2>Key Features</h2><p>L'assurance d'obtenir</p></div></div>

<div class="abs feat-card" style="left:99px;background:var(--c-vie)">Assurance Vie</div>
<div class="abs feat-icon" style="left:167px;background:var(--c-vie)"><svg width="46" height="46" viewBox="0 0 46 46" fill="none" stroke="#fff" stroke-width="2.5"><path d="M23 5 38 11v10c0 10-7 17-15 20C15 38 8 31 8 21V11z"/><path d="M16 22h14M23 15v14"/></svg></div>
<div class="abs feat-cta" style="left:99px">SOUMISSIONNEZ</div>

<div class="abs feat-card" style="left:354px;background:var(--c-salaire)">Salarie</div>
<div class="abs feat-icon" style="left:422px;background:var(--c-salaire)"><svg width="46" height="46" viewBox="0 0 46 46" fill="none" stroke="#fff" stroke-width="2.5"><path d="M6 20a17 12 0 0 1 34 0z"/><path d="M23 20v16a3 3 0 0 1-6 0"/></svg></div>
<div class="abs feat-cta" style="left:354px">SOUMISSIONNEZ</div>

<div class="abs feat-card" style="left:610px;background:var(--c-hypo)">Hypothecaire</div>
<div class="abs feat-icon" style="left:678px;background:var(--c-hypo)"><svg width="46" height="46" viewBox="0 0 46 46" fill="none" stroke="#fff" stroke-width="2.5"><path d="M9 22 23 10l14 12"/><path d="M13 19v16h20V19"/><path d="M20 35v-9h6v9"/></svg></div>
<div class="abs feat-cta" style="left:610px">SOUMISSIONNEZ</div>

<div class="abs feat-card" style="left:865px;background:var(--c-graves)">Maladies Graves</div>
<div class="abs feat-icon" style="left:933px;background:var(--c-graves)"><svg width="46" height="46" viewBox="0 0 46 46" fill="none" stroke="#fff" stroke-width="2.5"><path d="M23 37S8 28 8 18a8 8 0 0 1 15-4 8 8 0 0 1 15 4c0 10-15 19-15 19z"/><path d="M14 22h6l2-4 3 7 2-3h5"/></svg></div>
<div class="abs feat-cta" style="left:865px">SOUMISSIONNEZ</div>

<!-- blog -->
<div class="abs sec-head" style="left:476px;top:1506px"><span class="dot"></span><div><h2 style="color:#222">Blog Posts</h2><p style="color:#555">Assurance vie permanente</p></div></div>

<article class="abs post" style="left:99px">
  <div class="ph" role="img" aria-label="Photo d'une famille allongée dans l'herbe devant une maison" style="background:linear-gradient(#7fb2e4,#a9d08a 60%,#6aa33f)"></div>
  <span class="date">▦ 02 NOV 2015 07</span>
  <h3>Comment Procéder</h3>
  <p>Il vous suffit de remplir le formulaire de soumission d'assurance en ligne ci-haut, en cliquant sous la catégorie</p>
  <span class="more">Read More ⟶</span>
</article>
<article class="abs post" style="left:447px">
  <div class="ph" role="img" aria-label="Photo d'un couple avec un enfant devant une maison moderne" style="background:linear-gradient(#cfd8dc,#9aa39b 55%,#6f8a55)"></div>
  <span class="date">▦ 02 NOV 2015 07</span>
  <h3>Des conseillers en sécurité</h3>
  <p>L'équipe de lepontdoriole.ca vous offre un service novateur dans le domaine de l'assurance. Grâce à nos</p>
  <span class="more">Read More ⟶</span>
</article>
<article class="abs post" style="left:794px">
  <div class="ph" role="img" aria-label="Photo d'une famille devant une maison de banlieue" style="background:linear-gradient(#dfe6ea,#b5b9b0 55%,#7ea25a)"></div>
  <span class="date">▦ 02 NOV 2015 07</span>
  <h3>L'importance de ne pas payer</h3>
  <p>Débourser mensuellement ou annuellement de l'argent pour une assurance est une dépense considérable.</p>
  <span class="more">Read More ⟶</span>
</article>

<!-- assurance vie -->
<section class="abs vie-band"></section>
<div class="abs vie-brand"><span class="brand-dot" style="width:44px;height:44px;flex:none"></span><span class="brand-name">lepontdoriole.ca</span></div>
<h2 class="abs vie-title">Assurance Vie</h2>
<p class="abs vie-sub">Pour bien protéger vos proches</p>
<p class="abs vie-text">Une police en assurance vie vous permet de ne pas vous soucier de ce qu'il adviendra à vos proches dans le cas de votre décès. Lorsque parfaitement adaptée à votre vie et à vos besoins, elle vous épargne des inquiétudes et prévient les imprévus financiers.</p>
<div class="abs vie-ticks" style="left:388px;top:2234px"><svg width="18" height="18" viewBox="0 0 16 16" style="flex:none"><circle cx="8" cy="8" r="7" fill="none" stroke="#d9201f" stroke-width="1.5"/><path d="M4.5 8.2 7 10.5l4.5-5" fill="none" stroke="#d9201f" stroke-width="1.6"/></svg>Rente en cas d'invalidité</div>
<div class="abs vie-ticks" style="left:652px;top:2234px"><svg width="18" height="18" viewBox="0 0 16 16" style="flex:none"><circle cx="8" cy="8" r="7" fill="none" stroke="#d9201f" stroke-width="1.5"/><path d="M4.5 8.2 7 10.5l4.5-5" fill="none" stroke="#d9201f" stroke-width="1.6"/></svg>Protection en cas de décès ou mutilation accidentelle</div>
<div class="abs vie-ticks" style="left:388px;top:2284px;width:230px"><svg width="18" height="18" viewBox="0 0 16 16" style="flex:none"><circle cx="8" cy="8" r="7" fill="none" stroke="#d9201f" stroke-width="1.5"/><path d="M4.5 8.2 7 10.5l4.5-5" fill="none" stroke="#d9201f" stroke-width="1.6"/></svg>Protection en cas de fracture accidentelle</div>
<div class="abs vie-ticks" style="left:652px;top:2284px"><svg width="18" height="18" viewBox="0 0 16 16" style="flex:none"><circle cx="8" cy="8" r="7" fill="none" stroke="#d9201f" stroke-width="1.5"/><path d="M4.5 8.2 7 10.5l4.5-5" fill="none" stroke="#d9201f" stroke-width="1.6"/></svg>Assurance pour vos enfants</div>

<!-- contact strip -->
<svg class="abs" style="left:100px;top:2428px" width="36" height="36" viewBox="0 0 36 36" fill="none" stroke="#d9201f" stroke-width="2.4"><path d="M9 5h6l3 8-4 3c2 4 5 7 9 9l3-4 8 3v6c0 2-2 3-4 3C17 33 3 19 4 9c0-2 2-4 5-4z"/><path d="M22 6a9 9 0 0 1 8 8M22 12a3 3 0 0 1 3 3"/></svg>
<p class="abs contact-line" style="top:2424px">Il est parfois parfois intéressant de discuter directement avec<br>l'un de nos conseillers alors appeler nous au <strong>1-855-410-2276</strong></p>
<svg class="abs" style="left:100px;top:2496px" width="36" height="26" viewBox="0 0 36 26" fill="none" stroke="#d9201f" stroke-width="2.4"><rect x="2" y="2" width="32" height="22"/><path d="M2 2l16 13L34 2"/></svg>
<p class="abs contact-line" style="top:2486px">Il est toujours possible de nous faire parvenir vos commentaires par<br>courriel au <strong>contact@lepontdoriole.ca</strong>.</p>
<div class="abs partner-badge"><div style="width:80px;height:80px;background:#2a2a2a"></div><div style="width:200px;height:2px;background:#333"></div></div>

<!-- footer -->
<footer class="abs footer"></footer>
<div class="abs" style="left:116px;top:2660px;width:200px;display:flex;align-items:center;gap:10px"><span class="brand-dot" style="width:32px;height:32px;flex:none"></span><span class="brand-name" style="font-size:17px">lepontdoriole.ca</span></div>

<h4 class="abs f-h" style="left:357px;top:2614px">CONTACT US</h4>
<svg class="abs" style="left:357px;top:2666px" width="24" height="24" viewBox="0 0 24 24"><circle cx="12" cy="12" r="11" fill="none" stroke="#fff" stroke-width="1.5"/><path d="M12 6a4 4 0 0 1 4 4c0 3-4 8-4 8s-4-5-4-8a4 4 0 0 1 4-4z" fill="#fff"/></svg>
<p class="abs f-item" style="left:396px;top:2664px;width:220px"><b>Address:</b><br>Riverside Business Park, 412<br>Harbour High Rd, London</p>
<svg class="abs" style="left:357px;top:2730px" width="24" height="24" viewBox="0 0 24 24"><circle cx="12" cy="12" r="11" fill="none" stroke="#fff" stroke-width="1.5"/><rect x="6.5" y="8" width="11" height="8" fill="none" stroke="#fff" stroke-width="1.4"/><path d="M6.5 8l5.5 4.5L17.5 8" fill="none" stroke="#fff" stroke-width="1.4"/></svg>
<p class="abs f-item" style="left:396px;top:2730px;width:160px">Email: contact@lepont<br>doriole.ca</p>
<svg class="abs" style="left:357px;top:2792px" width="24" height="24" viewBox="0 0 24 24"><circle cx="12" cy="12" r="11" fill="none" stroke="#fff" stroke-width="1.5"/><path d="M8.5 6.5h2.5l1 3-1.5 1.2c.8 1.5 1.8 2.5 3.3 3.3l1.2-1.5 3 1v2.5c0 .7-.6 1.2-1.3 1.2C10.5 17 7 13.5 7.3 7.8c0-.7.5-1.3 1.2-1.3z" fill="#fff"/></svg>
<p class="abs f-item" style="left:396px;top:2795px">Phone: +1-855-410-2276</p>

<h4 class="abs f-h" style="left:650px;top:2614px">TERMS &amp; CONDITIONS</h4>
<ul class="abs f-list" style="left:650px;top:2662px">
  <li>&gt; Home</li><li>&gt; Products</li><li>&gt; Submission</li><li>&gt; Who We Are</li><li>&gt; Contact us</li>
</ul>

<h4 class="abs f-h" style="left:876px;top:2614px">NEWS LETTER</h4>
<div class="abs f-in" style="left:876px;top:2666px">Name</div>
<div class="abs f-in" style="left:876px;top:2712px">Email</div>
<div class="abs f-btn" style="left:876px;top:2758px">CONTACT US NOW</div>

<div class="abs bottom">© 2016 Lepontdoriole.ca. All Rights Reserved</div>

</body>
</html>
```